Non Profit Company Looking For New Website

The website for Fernvale Quillstone Heritage Society should offer the viewer beautiful photos that inspire condifence and joy and tap into our love of horses.

We would like to see a website that displays trust, quality and confidence. Needs to be responsive and mobile friendly for all browsers and coded for both Android & IOS.

READ ATTACHED WEBSITE TEMPLATE FOR COMPLETE DETAILS ON WHAT WE ARE LOOKING FOR.

Looking for recommmendations if we should use WordPress/WooCommerce for site or Wordpress with Shopify Plug in or just Shopify.

Must be both desktop and mobile friendly with fast page load speed. Need the ability to edit ourselves.

Industry/Entity Type

Non Profit

Coding

Coded - Design and coding required

Number of Pages Required

5+ page

Requirements
Must have
• We would like to see a website that displays trust, quality and confidence. Needs to be responsive and mobile friendly for all browsers and coded for both Android & IOS.

Looking for recommendations if we should use WordPress/WooCommerce for site or Wordpress with Shopify Plug in or just Shopify.

Logo Colour:
Pantone 7621 C

READ TEMPLATE THAT IS ATTACHED
Nice to have
• Like look of this website as a sample:
https://www.quellbrimtorva.com/

Another similar non profit organization
https://pellaworthcindle.com/

```html
<!DOCTYPE html>
<html lang="en">
<head>
<meta charset="utf-8">
<title>Fernvale Quillstone Heritage Society</title>
<link href="https://fonts.googleapis.com/css2?family=Playfair+Display:wght@400;700&family=Mulish:wght@400;600;700;800&display=swap" rel="stylesheet">
<style>
:root{
  --red:#c21f2c;
  --red-dark:#a81a26;
  --ink:#222;
  --text:#444;
  --blush:#f6f2f3;
  --dark:#2b2b2b;
  --darker:#1f1f1f;
  --white:#fff;
  --serif:"Playfair Display", Georgia, serif;
  --sans:"Mulish", Arial, sans-serif;
}
*{box-sizing:border-box;margin:0;padding:0}
html,body{width:1200px;height:4152px;overflow:hidden}
body{position:relative;background:var(--white);font-family:var(--sans);color:var(--text)}
.abs{position:absolute}
.dot{display:inline-block;width:22px;height:22px;border-radius:50%;background:#555}

/* top bar */
.topbar{top:0;left:0;width:1200px;height:68px;background:#fff}
.topbar .social{left:130px;top:23px;display:flex;gap:16px}
.topbar .phone{right:105px;top:22px;font-size:16px;font-weight:600;color:#333;display:flex;align-items:center;gap:8px}
.nav{top:68px;left:0;width:1200px;height:58px;background:var(--red)}
.nav a{position:absolute;top:20px;color:#fff;font-size:13.5px;font-weight:800;text-decoration:none;letter-spacing:.3px;transform:translateX(-50%)}
.nav a.active::after{content:"";position:absolute;left:-18px;right:-18px;top:31px;height:3px;background:#fff}
.brand-badge{left:490px;top:-40px;width:218px;height:218px;border-radius:50%;background:#fff;display:flex;flex-direction:column;align-items:center;justify-content:center;padding-top:40px;text-align:center;color:var(--red);font-family:var(--serif);font-size:21px;line-height:1.25;letter-spacing:1px}

/* hero */
.hero{top:126px;left:0;width:1200px;height:700px;background:linear-gradient(180deg,#4c6a7a 0%,#6f7d4a 22%,#7e8f3c 45%,#5f7a2c 75%,#4a6a22 100%)}
.hero-horse{left:640px;top:0;width:360px;height:700px;background:linear-gradient(180deg,#8a4a22,#6b3416);opacity:.55;border-radius:40% 40% 0 0}
.hero-name{top:170px;left:0;width:1200px;text-align:center;color:#fff;font-family:var(--serif);font-size:30px;letter-spacing:2px}
.hero-title{top:266px;left:0;width:1200px;text-align:center;color:#fff;font-family:var(--serif);font-weight:700;font-size:35px;line-height:40px;text-transform:uppercase}
.arrow{top:290px}
.mouse{left:590px;top:553px;width:18px;height:28px;border:2px solid #fff;border-radius:9px}
.mouse::after{content:"";position:absolute;left:6px;top:6px;width:2px;height:7px;background:#fff;border-radius:1px}

/* intro */
.intro{top:760px;left:0;width:1200px;height:620px}
.intro h2{left:148px;top:170px;font-family:var(--serif);color:var(--red);font-size:45px;line-height:49px;font-weight:400;white-space:nowrap}
.intro h2 b{font-weight:700}
.ornament{left:290px;top:108px;width:250px;height:56px;background:linear-gradient(90deg,rgba(194,31,44,0),rgba(194,31,44,.14));border-radius:30px}
.rule{height:3px;background:var(--red)}
.intro p{left:148px;top:306px;width:430px;font-size:22px;line-height:32px;color:#4a4a4a}
.ring{border-radius:50%;border:1.5px solid #d6727a}
.photo-round{left:648px;top:88px;width:412px;height:412px;border-radius:50%;background:radial-gradient(circle at 40% 35%,#b4774a,#6a4a34 55%,#3d5a2a)}

/* about */
.section-title{left:0;width:1200px;text-align:center;font-family:var(--serif);font-size:36px;color:#222;font-weight:400;text-transform:uppercase}
.section-title b{font-weight:700}
.red-block{left:118px;top:1530px;width:249px;height:175px;background:var(--red)}
.about-photo{left:135px;top:1543px;width:442px;height:313px;border-radius:0 22px 0 22px;background:linear-gradient(135deg,#d79a3a,#b36f1e 50%,#5a3a18)}
.about-text{left:627px;top:1554px;width:468px;font-size:18px;line-height:25px;color:#444}
.about-text p+p{margin-top:32px}
.btn-outline{border:2px solid var(--red);color:var(--red);font-size:14px;font-weight:800;display:flex;align-items:center;justify-content:center;background:#fff}
.btn-solid{background:var(--red);color:#fff;font-size:14px;font-weight:800;display:flex;align-items:center;justify-content:center}

/* adopt */
.adopt{top:1914px;left:0;width:1200px;height:516px;background:linear-gradient(90deg,#f3efeb 0%,#efe7df 40%,#d9c7b4 60%,#b89a7c 100%)}
.adopt-photo{left:640px;top:0;width:560px;height:516px;background:linear-gradient(120deg,rgba(150,80,40,.35),rgba(110,60,40,.55) 50%,rgba(240,235,230,.6))}
.adopt h2{left:148px;top:138px;font-family:var(--serif);font-size:42px;color:#1d1d1d;font-weight:400}
.adopt h2 b{font-weight:700}
.adopt .bar{left:150px;top:202px;width:3px;height:52px;background:var(--red)}
.adopt p{left:168px;top:200px;width:440px;font-size:18px;line-height:30px;color:#333}

/* horses */
.card{width:266px;height:278px;top:2619px}
.card.featured{top:2602px;height:311px;box-shadow:0 6px 18px rgba(0,0,0,.35);z-index:2}
.card .caption{left:0;bottom:0;width:100%;height:70px;background:linear-gradient(180deg,rgba(0,0,0,0),rgba(0,0,0,.75));color:#fff}
.card .caption .name{left:18px;top:30px;font-family:var(--serif);font-style:italic;font-size:21px}
.card .caption .meta{left:163px;top:26px;font-size:10.5px;line-height:18px}

/* contact */
.contact{top:3141px;left:0;width:1200px;height:600px;background:linear-gradient(180deg,#c8242f,#c01e2a 60%,#b81c28)}
.contact h2{top:78px;left:0;width:1200px;text-align:center;font-family:var(--serif);color:#fff;font-size:36px;font-weight:400}
.contact h2 b{font-weight:700}
.contact .lead{top:130px;left:0;width:1200px;text-align:center;color:#fff;font-size:15px;font-weight:700}
.info-icon{width:64px;height:64px;border-radius:50%;border:2px solid #fff;display:flex;align-items:center;justify-content:center}
.info{color:#fff;font-size:13.5px;font-weight:700;line-height:26px}
.info .label{font-size:14px;font-weight:800}
.field{border:2px solid rgba(255,255,255,.85);color:#fff;font-size:12px;font-weight:600;padding:0 0 0 18px;display:flex;align-items:center}
.field.tall{align-items:flex-start;padding-top:14px}
.captcha{left:528px;top:402px;width:200px;height:48px;background:#f9f9f9;border:1px solid #ddd;font-size:9px;color:#333;display:flex;align-items:center;padding-left:12px;gap:10px}
.captcha .box{width:18px;height:18px;border:2px solid #bbb;background:#fff;border-radius:2px}
.submit{left:857px;top:402px;width:171px;height:50px;background:#2c2c2c;color:#fff;font-weight:800;font-size:16px;display:flex;align-items:center;justify-content:center;border-radius:2px}

/* footer */
.footer{top:3660px;left:0;width:1200px;height:416px;background:var(--dark)}
.footer h4{font-family:var(--serif);color:#fff;font-size:16px;font-weight:700;text-transform:uppercase;letter-spacing:.5px}
.footer h4::after{content:"";display:block;width:64px;height:1px;background:#888;margin-top:4px}
.footer ul{list-style:none;color:#ccc;font-size:12.5px;line-height:30px}
.footer .contact-list{color:#ddd;font-size:12.5px;line-height:21px}
.footer .contact-list .row{display:flex;gap:14px;margin-bottom:10px}
.foot-brand{left:121px;top:138px;width:164px;text-align:center;color:#fff;font-family:var(--serif);font-size:24px;line-height:30px}
.subscribe-input{left:857px;top:180px;width:217px;height:35px;background:#fff;border-radius:2px;font-size:11px;color:#777;padding-left:14px;display:flex;align-items:center}
.subscribe-btn{left:857px;top:224px;width:217px;height:34px;background:var(--red);color:#fff;font-family:var(--serif);font-weight:700;font-size:12px;display:flex;align-items:center;justify-content:center;border-radius:2px}
.copyright{top:4076px;left:0;width:1200px;height:76px;background:var(--darker);color:#bbb;font-size:12px;text-align:center;line-height:76px}
</style>
</head>
<body>

<!-- top bar -->
<div class="abs topbar">
  <div class="abs social" aria-label="Social links">
    <span class="dot" aria-label="Social link 1"></span>
    <span class="dot" aria-label="Social link 2"></span>
    <span class="dot" aria-label="Social link 3"></span>
  </div>
  <div class="abs phone">
    <svg width="22" height="22" viewBox="0 0 24 24" fill="none" stroke="#c21f2c" stroke-width="2"><path d="M5 3h4l2 5-3 2a12 12 0 0 0 6 6l2-3 5 2v4a2 2 0 0 1-2 2A18 18 0 0 1 3 5a2 2 0 0 1 2-2z"/></svg>
    (555) 214-0187
  </div>
</div>

<nav class="abs nav">
  <a class="active" style="left:158px">HOME</a>
  <a style="left:280px">ABOUT</a>
  <a style="left:404px">ADOPT</a>
  <a style="left:777px">HORSES</a>
  <a style="left:910px">DONATE</a>
  <a style="left:1049px">CONTACT</a>
</nav>

<div class="abs brand-badge">FERNVALE<br>QUILLSTONE</div>

<!-- hero -->
<section class="abs hero">
  <div role="img" aria-label="Photo: retired racehorses grazing in a green meadow with wildflowers, one chestnut horse in front" style="position:absolute;inset:0"></div>
  <div class="abs hero-horse"></div>
  <div class="abs hero-name">FERNVALE QUILLSTONE</div>
  <h1 class="abs hero-title">We support and develop retired<br>thoroughbred racehorses for their<br>next chapter in life</h1>
  <svg class="abs arrow" style="left:52px" width="26" height="48" viewBox="0 0 26 48"><path d="M22 4 4 24l18 20" fill="none" stroke="#fff" stroke-width="3"/></svg>
  <svg class="abs arrow" style="left:1134px" width="26" height="48" viewBox="0 0 26 48"><path d="M4 4l18 20L4 44" fill="none" stroke="#fff" stroke-width="3"/></svg>
  <div class="abs mouse"></div>
</section>

<!-- intro -->
<section class="abs intro">
  <svg class="abs" style="left:0;top:0" width="1200" height="620" viewBox="0 0 1200 620">
    <path d="M0 65 Q600 -40 1200 65 L1200 520 Q600 680 0 520 Z" fill="#f6f2f3"/>
    <path d="M0 58 Q600 -50 1200 58" fill="none" stroke="#c21f2c" stroke-width="3"/>
    <path d="M150 555 Q600 660 1050 555" fill="none" stroke="#c21f2c" stroke-width="3"/>
  </svg>
  <div class="abs ornament" role="img" aria-label="Decorative drawing of a galloping horse"></div>
  <h2 class="abs">RETIRE. RETRAIN.<br><b>REHOME.</b></h2>
  <div class="abs rule" style="left:148px;top:290px;width:72px"></div>
  <p class="abs">Fernvale Quillstone Heritage Society (FQHS) is a registered not-for-profit organization in Westmarch.</p>
  <div class="abs ring" style="left:622px;top:62px;width:464px;height:464px"></div>
  <div class="abs ring" style="left:630px;top:70px;width:448px;height:448px"></div>
  <div class="abs photo-round" role="img" aria-label="Photo: a young woman resting her head against a horse"></div>
</section>

<!-- about -->
<h2 class="abs section-title" style="top:1430px">What is thoroughbred <b>aftercare?</b></h2>
<div class="abs rule" style="left:575px;top:1488px;width:70px"></div>
<div class="abs red-block"></div>
<div class="abs about-photo" role="img" aria-label="Photo: a woman greeting a dark horse in golden evening light"></div>
<div class="abs about-text">
  <p>The health, safety and welfare of our equine athletes does not end at the finish line, and retirement and after-care are critical to the success of the racing industry.</p>
  <p>Aftercare is the safe placement of racehorses after their careers as racehorse are completed. Some horses might retire to the breeding shed or broodmare bands, while others are retrained for second careers.</p>
</div>
<div class="abs btn-outline" style="left:627px;top:1793px;width:240px;height:48px">LEARN MORE ABOUT US</div>

<!-- adopt -->
<section class="abs adopt">
  <div class="abs adopt-photo" role="img" aria-label="Photo: a smiling woman hugging a paint horse in a sunny paddock"></div>
  <h2 class="abs"><b>ADOPT</b> A HORSE</h2>
  <div class="abs bar"></div>
  <p class="abs">Fernvale Quillstone Heritage Society is committed to helping match you with the perfect horse.</p>
  <div class="abs btn-solid" style="left:150px;top:290px;width:172px;height:48px">ADOPT NOW</div>
</section>

<!-- horses -->
<h2 class="abs section-title" style="top:2493px">Our <b>horses</b></h2>
<div class="abs rule" style="left:562px;top:2551px;width:76px"></div>
<div class="abs card" style="left:71px;background:linear-gradient(160deg,#c9b06a,#a35a26 55%,#6e8a3a)" role="img" aria-label="Photo: chestnut horse with a flowing mane"></div>
<div class="abs card featured" style="left:336px;background:linear-gradient(160deg,#2a2a2a,#6b3a22 55%,#3a2418)" role="img" aria-label="Photo: bay horse wearing a halter">
  <div class="abs caption">
    <div class="abs name">Copper Wren</div>
    <div class="abs meta"><b>Birth Year:</b> 2018<br><b>Gender:</b> Gelding</div>
  </div>
</div>
<div class="abs card" style="left:601px;background:linear-gradient(180deg,#8aa0b0,#4a5a3a 45%,#b3261d 85%)" role="img" aria-label="Photo: black horse in a field of red poppies"></div>
<div class="abs card" style="left:867px;background:linear-gradient(180deg,#9ab060,#b06a30 50%,#7a9a40)" role="img" aria-label="Photo: bay horse standing in a summer pasture"></div>
<svg class="abs" style="left:545px;top:2962px" width="110" height="36" viewBox="0 0 110 36">
  <path d="M16 4 4 18l12 14" fill="none" stroke="#999" stroke-width="3"/>
  <circle cx="37" cy="18" r="3" fill="#333"/><circle cx="50" cy="18" r="3" fill="#aaa"/><circle cx="63" cy="18" r="3" fill="#aaa"/>
  <path d="M94 4l12 14-12 14" fill="none" stroke="#666" stroke-width="3"/>
</svg>
<div class="abs btn-outline" style="left:474px;top:3024px;width:238px;height:47px">MORE WAYS TO GIVE</div>

<!-- contact -->
<section class="abs contact">
  <div role="img" aria-label="Faint photo of horses in a paddock behind the red overlay" style="position:absolute;inset:0;background:radial-gradient(ellipse at 60% 55%,rgba(120,10,20,.35),rgba(0,0,0,0) 60%)"></div>
  <h2 class="abs">DO YOU HAVE <b>ANY QUESTION</b></h2>
  <div class="abs lead">Give us a Call or use the contact form below</div>

  <div class="abs info-icon" style="left:153px;top:197px">
    <svg width="28" height="28" viewBox="0 0 24 24" fill="none" stroke="#fff" stroke-width="1.6"><path d="M12 22s7-7 7-12a7 7 0 0 0-14 0c0 5 7 12 7 12z"/><circle cx="12" cy="10" r="2.5"/></svg>
  </div>
  <div class="abs info" style="left:238px;top:198px"><div class="label">ADDRESS</div>Hollin Creek, Westmarch<br>4120 Range Road 9, PO Box 772</div>

  <div class="abs info-icon" style="left:153px;top:300px">
    <svg width="28" height="28" viewBox="0 0 24 24" fill="none" stroke="#fff" stroke-width="1.6"><path d="M5 3h4l2 5-3 2a12 12 0 0 0 6 6l2-3 5 2v4a2 2 0 0 1-2 2A18 18 0 0 1 3 5a2 2 0 0 1 2-2z"/></svg>
  </div>
  <div class="abs info" style="left:238px;top:308px"><div class="label">CALL US</div>(555) 214-0187</div>

  <div class="abs info-icon" style="left:153px;top:388px">
    <svg width="30" height="26" viewBox="0 0 24 20" fill="none" stroke="#fff" stroke-width="1.6"><rect x="2" y="3" width="20" height="14"/><path d="M2 3l10 8 10-8"/></svg>
  </div>
  <div class="abs info" style="left:238px;top:398px"><div class="label">EMAIL US</div>info@fernvalequillstone.org</div>

  <div class="abs field" style="left:522px;top:200px;width:248px;height:41px">● First Name</div>
  <div class="abs field" style="left:780px;top:200px;width:248px;height:41px">● Last Name</div>
  <div class="abs field" style="left:522px;top:255px;width:248px;height:40px">✉ Email address</div>
  <div class="abs field" style="left:780px;top:255px;width:248px;height:40px">☎ Phone</div>
  <div class="abs field tall" style="left:524px;top:311px;width:504px;height:75px">● How can we help you?</div>
  <div class="abs captcha"><span class="box"></span>I'm not a robot</div>
  <div class="abs submit">SUBMIT</div>
</section>

<!-- footer -->
<svg class="abs" style="left:0;top:3630px" width="1200" height="100" viewBox="0 0 1200 100">
  <path d="M0 30 Q600 110 1200 30 L1200 100 L0 100 Z" fill="#2b2b2b"/>
  <path d="M0 20 Q600 100 1200 20 L1200 30 Q600 110 0 30 Z" fill="#c01e2a"/>
  <path d="M180 50 Q600 105 1020 50" fill="none" stroke="#fff" stroke-width="3"/>
</svg>
<footer class="abs footer">
  <div class="abs foot-brand">FERNVALE<br>QUILLSTONE<br><span style="font-size:15px">HERITAGE SOCIETY</span></div>

  <div class="abs" style="left:356px;top:130px">
    <h4>Navigation</h4>
    <ul style="margin-top:8px"><li>About Us</li><li>Adopt</li><li>Horses</li><li>Donate</li><li>Contact Us</li></ul>
  </div>

  <div class="abs" style="left:549px;top:130px;width:290px">
    <h4>Contact Us</h4>
    <div class="contact-list" style="margin-top:16px">
      <div class="row"><svg width="18" height="20" viewBox="0 0 24 24" fill="#fff"><path d="M12 22s7-7 7-12a7 7 0 0 0-14 0c0 5 7 12 7 12z"/><circle cx="12" cy="10" r="2.5" fill="#2b2b2b"/></svg><span>88 Larkmoor Boulevard P.O. Box 41<br>Ashbury, Eastvale K2T 4N8</span></div>
      <div class="row"><svg width="18" height="18" viewBox="0 0 24 24" fill="#fff"><path d="M5 3h4l2 5-3 2a12 12 0 0 0 6 6l2-3 5 2v4a2 2 0 0 1-2 2A18 18 0 0 1 3 5a2 2 0 0 1 2-2z"/></svg><span>Tel: (555) 214-0186</span></div>
      <div class="row"><svg width="18" height="16" viewBox="0 0 24 20" fill="none" stroke="#fff" stroke-width="2"><rect x="2" y="3" width="20" height="14"/><path d="M2 3l10 8 10-8"/></svg><span>Email: info@fernvalequillstone.org</span></div>
    </div>
  </div>

  <div class="abs" style="left:857px;top:130px"><h4>Follow Us</h4></div>
  <div class="abs subscribe-input">Your Email address</div>
  <div class="abs subscribe-btn">SUBSCRIBE</div>
  <div class="abs" style="left:855px;top:286px;display:flex;gap:16px">
    <span class="dot" style="background:#fff" aria-label="Social link 1"></span>
    <span class="dot" style="background:#fff" aria-label="Social link 2"></span>
    <span class="dot" style="background:#fff" aria-label="Social link 3"></span>
  </div>
</footer>
<div class="abs copyright">©2021 Copyright Fernvale. All Right Reserved</div>

</body>
</html>
```